App-Design für Vergleichsportal für Reparaturen
Zielgruppe
Flickwerkzentrale ist das Vergleichsportal für Reparaturen in deiner Nähe. Egal ob du eine Werkstatt für dein Smartphone, Tablet, Laptop, Computer, Smartwatch oder Spielkonsole suchst. Mit uns findest du deine passende Reparaturwerkstat in deiner Nähe mit dem besten Preis für dich. Du kannst dich direkt über unser Portal deinen Reparaturauftrag erhalten und wirst durch unser Sicher Kaufen Käuferschutz und unser VORMANT Treuhandschutz abgesichert.
Aufgabenstellung
Unter Flickwerkzentrale.de kann das aktuelle Design angeschaut werden. Die Farbe sollten übernommen werden.
Über die Startseite kann der Kunde sein Gerät, Service sowie seine Adresse eingeben. Auf der Vergleichsseite bekommt der Kunde die Übersicht welche Reparaturwerkstätten es gibt, zu welche Preisen die ausgewählte Dienstleistung angeboten wird. Wenn der Kunde auf den Button 'Jetzt Online Bestpreis buchen' drückt, dann kommt der Kunde in den Warenkorb. Im Warenkorb können noch weitere Dienstleistungen und Produkte dazugebucht werden. Und anschließend kommt der Kunde in die Kasse und kann der Bestellvorgang beenden. Die Benutzerführung sollte einfach sein. Im Fokus steht die Vergleichsseite. Dort sollte der Kunde ca. 4 Werkstätten auf einen Blick sehen können. Könnte ausschauen wie bei Tarifblick in der Kategorie Mobilfunk.
Die Vergleichseite sollte auf jeden Fall folgende Elemente enthalten:
- Entfernung zur Werkstatt in Meter bzw. Kilometer
- Logo der Werkstatt
- Name der Werkstatt
- Bewertungssterne der Werkstatt
- Reparaturzeit und Ersatzeilverfügbarkeit
- Reparaturpreis (Platz sollte auch bei Auswahl von 2 Dienstleistungen vorhanden sein)
- Rabattanzeige
- Qualitätssiegel (noch nicht vorhanden)
- Anzeige von Verknappung (z. B. noch 3 Termin frei)
- Qualitätsmerkmale (z. B. 12 Monate Garantie)
Die Merkmale Öffnungszeiten, Adresse, Kostenpflichtige Zusatzleistungen können aus Platzgründen in den Warenkorbseite wandern außer es gibt eine schöne und einfache Lösung.
In der Warenkorbseite kann dazu auch die Tarifblick Seite dienen.
Bei allen sollte auf die Benutzerfreundlichkeit geachtet werden.
Bei offenen Frage stehe ich zur Verfügung und freue mich auf viele Designs.
Vielen DANK im Voraus!

```html
<!DOCTYPE html>
<html lang="de">
<head>
<meta charset="utf-8">
<title>Flickwerkzentrale – Vergleichsseite</title>
<link href="https://fonts.googleapis.com/css2?family=Open+Sans:wght@300;400;600&display=swap" rel="stylesheet">
<style>
:root{
  --stage:#262626;
  --band:#2a4a5c;
  --green:#8cc63f;
  --green-dark:#6ea62b;
  --red:#d0021b;
  --text:#333a3f;
  --muted:#5d666c;
  --page:#eef0f2;
  --star:#f7c600;
  --star-off:#dcdcdc;
  --white:#fff;
}
*{box-sizing:border-box;margin:0;padding:0}
html,body{width:1200px;height:728px;overflow:hidden}
body{background:var(--stage);font-family:"Open Sans",Arial,sans-serif;color:var(--text);position:relative}
.screen-wrap{position:absolute;left:439px;top:16px;width:322px;height:696px}
.screen{width:402px;height:870px;transform:scale(.8);transform-origin:0 0;background:var(--page);position:relative;overflow:hidden}
.status-bar{position:absolute;left:0;top:0;width:100%;height:30px;background:var(--white)}
.status-time{position:absolute;left:19px;top:6px;font-size:14px;font-weight:600;letter-spacing:.5px}
.status-icons{position:absolute;right:14px;top:9px}
.app-header{position:absolute;left:0;top:30px;width:100%;height:58px;background:var(--white);box-shadow:0 1px 2px rgba(0,0,0,.08)}
.brand{position:absolute;left:16px;top:18px;display:flex;align-items:center;gap:6px;font-size:17px;font-weight:400;color:var(--band)}
.brand-dot{width:12px;height:12px;border-radius:50%;background:var(--green)}
.menu-toggle{position:absolute;right:15px;top:20px;width:24px}
.menu-toggle span{display:block;height:2px;background:var(--band);margin-bottom:6px}
.breadcrumb{position:absolute;left:31px;right:32px;top:97px;display:flex;justify-content:space-between;font-size:10px}
.breadcrumb .edit{color:var(--green-dark);display:flex;align-items:center;gap:3px}
.card{position:absolute;left:31px;width:339px;background:var(--white)}
.card-band{height:31px;background:var(--band);color:var(--white);font-size:11px;display:flex;align-items:center;justify-content:center;position:relative}
.card-band::after{content:"";position:absolute;left:12px;right:12px;bottom:6px;height:1px;background:rgba(140,198,63,.5)}
.card-band .pin{position:absolute;left:8px;top:8px}
.card-band .flag{position:absolute;right:12px;top:8px}
.card-body{position:relative;height:207px}
.shop-name{position:absolute;left:12px;top:7px;font-size:13px}
.shop-logo{position:absolute;left:12px;top:32px;display:flex;align-items:center;gap:6px;font-size:16px;font-weight:600;color:var(--band)}
.shop-logo i{width:18px;height:18px;background:var(--band)}
.discount{position:absolute;left:168px;top:22px;display:flex;align-items:center;gap:6px;font-size:8.5px;line-height:10px;color:var(--green-dark)}
.price{position:absolute;right:12px;text-align:right}
.price .old{font-size:18px;color:var(--band);text-decoration:line-through;line-height:22px}
.price .new{font-size:22px;color:var(--red);line-height:26px}
.rating{position:absolute;left:12px;top:64px;display:flex;align-items:center;gap:4px;font-size:12px;color:var(--green-dark)}
.scarcity{position:absolute;right:12px;top:63px;display:flex;align-items:center;gap:8px;font-size:12px;color:var(--red)}
.address{position:absolute;left:12px;top:93px;display:flex;gap:5px;font-size:9.5px;line-height:13px;color:var(--muted)}
.divider{position:absolute;left:134px;top:93px;width:1px;height:26px;background:#999}
.facts{position:absolute;left:157px;right:12px;top:93px;font-size:9.5px;line-height:13px;color:var(--muted)}
.facts div{display:flex;justify-content:space-between}
.facts b{font-weight:400;color:var(--green-dark)}
.facts b.no,.feature.no{color:var(--red)}
.features{position:absolute;left:14px;right:12px;top:132px;display:flex;justify-content:space-between;font-size:9px;color:var(--text)}
.feature{display:flex;align-items:center;gap:5px}
.book-btn{position:absolute;left:12px;right:12px;top:162px;height:35px;background:var(--green);color:var(--white);font-size:15px;display:flex;align-items:center;justify-content:center;gap:10px}
</style>
</head>
<body>
<svg width="0" height="0" style="position:absolute">
  <defs>
    <symbol id="star" viewBox="0 0 24 24"><path d="M12 1.5l3.2 6.8 7.3.9-5.4 5.1 1.4 7.3L12 18l-6.5 3.6 1.4-7.3L1.5 9.2l7.3-.9z"/></symbol>
    <symbol id="pin" viewBox="0 0 12 16"><path d="M6 0a5 5 0 0 0-5 5c0 4 5 11 5 11s5-7 5-11a5 5 0 0 0-5-5zm0 7a2 2 0 1 1 0-4 2 2 0 0 1 0 4z"/></symbol>
    <symbol id="percent" viewBox="0 0 20 20"><circle cx="10" cy="10" r="8.5" fill="none" stroke="currentColor" stroke-width="1.4" stroke-dasharray="3 1.5"/><path d="M6.5 13.5l7-7" stroke="currentColor" stroke-width="1.4"/><circle cx="7" cy="7" r="1.3" fill="currentColor"/><circle cx="13" cy="13" r="1.3" fill="currentColor"/></symbol>
    <symbol id="warn" viewBox="0 0 20 18"><path d="M10 1L19 17H1z" fill="none" stroke="currentColor" stroke-width="1.6" stroke-linejoin="round"/><path d="M10 6.5v5.5" stroke="currentColor" stroke-width="1.8"/><circle cx="10" cy="14.2" r="1" fill="currentColor"/></symbol>
    <symbol id="truck" viewBox="0 0 22 14"><path d="M1 2h12v9H1zM13 5h4l3 3v3h-7" fill="none" stroke="currentColor" stroke-width="1.2"/><circle cx="5" cy="12" r="1.6" fill="#fff" stroke="currentColor"/><circle cx="16" cy="12" r="1.6" fill="#fff" stroke="currentColor"/></symbol>
    <symbol id="spark" viewBox="0 0 18 18"><path d="M9 1v4M9 13v4M1 9h4M13 9h4M3.5 3.5l2.5 2.5M12 12l2.5 2.5M14.5 3.5L12 6M6 12l-2.5 2.5" stroke="currentColor" stroke-width="1.3" fill="none"/></symbol>
    <symbol id="seal" viewBox="0 0 16 20"><circle cx="8" cy="7" r="6" fill="none" stroke="currentColor" stroke-width="1.3"/><circle cx="8" cy="7" r="3" fill="none" stroke="currentColor" stroke-width="1"/><path d="M4.5 12l-2 7 3-1.5 1.5 2 1-6M11.5 12l2 7-3-1.5-1.5 2-1-6" fill="none" stroke="currentColor" stroke-width="1.1"/></symbol>
    <symbol id="cart" viewBox="0 0 22 18"><path d="M1 1h3l2.5 10h11l2-7H5" fill="none" stroke="currentColor" stroke-width="1.5" stroke-linejoin="round"/><path d="M8 6h10M8.5 8.5h9" stroke="currentColor" stroke-width="1"/><circle cx="8" cy="15" r="1.6" fill="currentColor"/><circle cx="16" cy="15" r="1.6" fill="currentColor"/></symbol>
    <symbol id="flag" viewBox="0 0 10 12"><path d="M1 0v12" stroke="currentColor" stroke-width="1.2"/><path d="M1.5 1h8l-2 2.5 2 2.5h-8z" fill="currentColor"/></symbol>
    <linearGradient id="half"><stop offset="50%" stop-color="#f7c600"/><stop offset="50%" stop-color="#dcdcdc"/></linearGradient>
  </defs>
</svg>

<div class="screen-wrap">
<main class="screen">
  <div class="status-bar">
    <span class="status-time">9:41</span>
    <svg class="status-icons" width="58" height="12" viewBox="0 0 58 12" aria-hidden="true">
      <g fill="#333a3f"><rect x="0" y="8" width="3" height="4"/><rect x="4.5" y="6" width="3" height="6"/><rect x="9" y="3" width="3" height="9"/><rect x="13.5" y="0" width="3" height="12"/></g>
      <path d="M22 4.5a9 9 0 0 1 12 0M24.5 7a5.5 5.5 0 0 1 7 0" stroke="#333a3f" stroke-width="1.6" fill="none"/><circle cx="28" cy="10" r="1.4" fill="#333a3f"/>
      <rect x="36.5" y="1" width="19" height="10" rx="2.5" fill="none" stroke="#333a3f"/><rect x="38.5" y="3" width="15" height="6" rx="1" fill="#333a3f"/><rect x="56" y="4" width="1.5" height="4" fill="#333a3f"/>
    </svg>
  </div>

  <header class="app-header">
    <div class="brand"><span class="brand-dot"></span>Flickwerkzentrale</div>
    <div class="menu-toggle"><span></span><span></span><span></span></div>
  </header>

  <nav class="breadcrumb">
    <span>Fonix 6s / Akku / Lindenplatz 4, München</span>
    <span class="edit"><svg width="9" height="9" viewBox="0 0 10 10"><path d="M1 9l1-3 5-5 2 2-5 5z" fill="#6ea62b"/></svg>Adresse ändern</span>
  </nav>

  <!-- Werkstatt 1 -->
  <article class="card" style="top:120px">
    <div class="card-band">
      <svg class="pin" width="10" height="13" fill="#8cc63f"><use href="#pin"/></svg>
      246 m von dir entfernt
      <svg class="flag" width="10" height="12" color="#8cc63f"><use href="#flag"/></svg>
    </div>
    <div class="card-body">
      <h2 class="shop-name" style="font-weight:400">Kovex Repair München</h2>
      <div class="shop-logo"><i></i>KOVEX</div>
      <div class="discount"><svg width="20" height="20"><use href="#percent"/></svg><span>-8,00€ Rabatt<br>endet in 13h</span></div>
      <div class="price" style="top:10px"><div class="old">87,00€</div><div class="new">79,00€</div></div>
      <div class="rating">
        <svg width="16" height="16" fill="var(--star)"><use href="#star"/></svg><svg width="16" height="16" fill="var(--star)"><use href="#star"/></svg><svg width="16" height="16" fill="var(--star)"><use href="#star"/></svg><svg width="16" height="16" fill="var(--star)"><use href="#star"/></svg><svg width="16" height="16" fill="var(--star)"><use href="#star"/></svg>
        <span>(5/5)</span>
      </div>
      <div class="scarcity"><svg width="20" height="18"><use href="#warn"/></svg>nur noch 3 Termine frei !</div>
      <div class="address"><svg width="9" height="12" fill="#8cc63f"><use href="#pin"/></svg><span>Ahornweg 12<br>80337 München</span></div>
      <div class="divider"></div>
      <div class="facts"><div><span>Reparaturzeit:</span><b>2 Tage</b></div><div><span>Ersatzteilverfügbarkeit:</span><b>Verfügbar</b></div></div>
      <div class="features">
        <span class="feature"><svg width="20" height="13" color="#8cc63f"><use href="#truck"/></svg>Versand möglich</span>
        <span class="feature"><svg width="16" height="16" color="#8cc63f"><use href="#spark"/></svg>12 Monate Garantie</span>
        <span class="feature"><svg width="14" height="18" color="#8cc63f"><use href="#seal"/></svg>Muster Siegel</span>
      </div>
      <a class="book-btn"><svg width="22" height="18" color="#fff"><use href="#cart"/></svg>Jetzt Online Bestpreis buchen</a>
    </div>
  </article>

  <!-- Werkstatt 2 -->
  <article class="card" style="top:369px">
    <div class="card-band">
      <svg class="pin" width="10" height="13" fill="#8cc63f"><use href="#pin"/></svg>
      762 m von dir entfernt
      <svg class="flag" width="10" height="12" color="#8cc63f"><use href="#flag"/></svg>
    </div>
    <div class="card-body">
      <h2 class="shop-name" style="font-weight:400">Geräteklinik München Giesing</h2>
      <div class="shop-logo"><i></i>Geräteklinik</div>
      <div class="price" style="top:20px"><div class="new">82,00€</div></div>
      <div class="rating">
        <svg width="16" height="16" fill="var(--star)"><use href="#star"/></svg><svg width="16" height="16" fill="var(--star)"><use href="#star"/></svg><svg width="16" height="16" fill="var(--star)"><use href="#star"/></svg><svg width="16" height="16" fill="url(#half)"><use href="#star"/></svg><svg width="16" height="16" fill="var(--star-off)"><use href="#star"/></svg>
        <span>(3,7/5)</span>
      </div>
      <div class="address"><svg width="9" height="12" fill="#8cc63f"><use href="#pin"/></svg><span>Ahornweg 12<br>80337 München</span></div>
      <div class="divider"></div>
      <div class="facts"><div><span>Reparaturzeit:</span><b>2 Tage</b></div><div><span>Ersatzteilverfügbarkeit:</span><b class="no">nicht verfügbar</b></div></div>
      <div class="features">
        <span class="feature no"><svg width="20" height="13" color="#8cc63f"><use href="#truck"/></svg>Versand nicht möglich</span>
        <span class="feature"><svg width="16" height="16" color="#8cc63f"><use href="#spark"/></svg>12 Monate Garantie</span>
        <span class="feature"><svg width="14" height="18" color="#8cc63f"><use href="#seal"/></svg>Muster Siegel</span>
      </div>
      <a class="book-btn"><svg width="22" height="18" color="#fff"><use href="#cart"/></svg>Jetzt Online Bestpreis buchen</a>
    </div>
  </article>

  <!-- Werkstatt 3 -->
  <article class="card" style="top:618px">
    <div class="card-band">
      <svg class="pin" width="10" height="13" fill="#8cc63f"><use href="#pin"/></svg>
      1,2 km von dir entfernt
      <svg class="flag" width="10" height="12" color="#8cc63f"><use href="#flag"/></svg>
    </div>
    <div class="card-body">
      <h2 class="shop-name" style="font-weight:400">Fixpunkt am Harras</h2>
      <div class="shop-logo"><i></i>Fixpunkt</div>
      <div class="discount"><svg width="20" height="20"><use href="#percent"/></svg><span>-11,00€ Rabatt<br>endet in 13h</span></div>
      <div class="price" style="top:10px"><div class="old">100,00€</div><div class="new">89,00€</div></div>
      <div class="rating">
        <svg width="16" height="16" fill="var(--star)"><use href="#star"/></svg><svg width="16" height="16" fill="var(--star)"><use href="#star"/></svg><svg width="16" height="16" fill="var(--star)"><use href="#star"/></svg><svg width="16" height="16" fill="var(--star)"><use href="#star"/></svg><svg width="16" height="16" fill="var(--star)"><use href="#star"/></svg>
        <span>(5/5)</span>
      </div>
      <div class="scarcity"><svg width="20" height="18"><use href="#warn"/></svg>nur noch 4 Termine frei !</div>
      <div class="address"><svg width="9" height="12" fill="#8cc63f"><use href="#pin"/></svg><span>Ahornweg 12<br>80337 München</span></div>
      <div class="divider"></div>
      <div class="facts"><div><span>Reparaturzeit:</span><b>2 Tage</b></div><div><span>Ersatzteilverfügbarkeit:</span><b>Verfügbar</b></div></div>
      <div class="features">
        <span class="feature"><svg width="20" height="13" color="#8cc63f"><use href="#truck"/></svg>Versand möglich</span>
        <span class="feature"><svg width="16" height="16" color="#8cc63f"><use href="#spark"/></svg>12 Monate Garantie</span>
        <span class="feature"><svg width="14" height="18" color="#8cc63f"><use href="#seal"/></svg>Muster Siegel</span>
      </div>
      <a class="book-btn"><svg width="22" height="18" color="#fff"><use href="#cart"/></svg>Jetzt Online Bestpreis buchen</a>
    </div>
  </article>
</main>
</div>
</body>
</html>
```